Dusty Spur Outfitters Home Page

I need a logo and page design for my home page, maybe some background color suggestions to go with it. I want the logo to project "vintage" and "western wear" but not be your typical trite western saddle and gun type thing.
http://www.dustyspuroutfitters.example/store/cart.php
Not looking for page coding just logo and other design elements to lay in over the site's template to make it "pop"
Reason: Have to finalize the design.
Target Market(s)
My customers are 70/30 men to women.
Industry/Entity Type
Gun

```html
<!DOCTYPE html>
<html lang="en">
<head>
<meta charset="utf-8">
<title>Dusty Spur Outfitters – Header Variations</title>
<link href="https://fonts.googleapis.com/css2?family=Lato:wght@700&family=Damion&display=swap" rel="stylesheet">
<style>
  :root {
    --linen: #cfbd9d;
    --linen-light: #d6c6a8;
    --leather: #56201a;
    --leather-dark: #3f1712;
    --trim-brown: #3a1712;
    --trim-charcoal: #262322;
    --trim-blue: #4a87a2;
    --cream: #e6dac0;
    --tagline: #d9d3bf;
    --ink: #2f2b27;
  }
  * { margin: 0; padding: 0; box-sizing: border-box; }
  html, body { width: 1200px; height: 1000px; overflow: hidden; }
  body {
    position: relative;
    background: repeating-linear-gradient(0deg, var(--linen) 0 2px, var(--linen-light) 2px 4px);
    font-family: "Lato", sans-serif;
  }
  .header-variant {
    position: absolute;
    left: 0;
    width: 1200px;
    height: 165px;
    box-shadow: 0 3px 5px rgba(0,0,0,.35);
  }
  .header-variant--brown { top: 148px; background: var(--trim-brown); }
  .header-variant--charcoal { top: 418px; background: var(--trim-charcoal); }
  .header-variant--blue { top: 688px; background: var(--trim-blue); }

  .header-panel {
    position: absolute;
    left: 0; right: 0;
    top: 15px; bottom: 17px;
    background:
      radial-gradient(ellipse at 30% 40%, rgba(120,45,35,.35), transparent 60%),
      radial-gradient(ellipse at 75% 60%, rgba(110,40,30,.3), transparent 55%),
      var(--leather);
    box-shadow: inset 0 2px 4px rgba(0,0,0,.4), inset 0 -2px 4px rgba(0,0,0,.4);
  }
  .header-variant--brown .header-panel { background-color: var(--leather); }

  .brand {
    position: absolute;
    left: 60px; top: 48px;
    display: flex; align-items: center; gap: 14px;
    font-weight: 700;
    font-size: 34px;
    color: var(--cream);
    white-space: nowrap;
  }
  .brand-mark {
    width: 22px; height: 22px;
    background: var(--cream);
  }
  .tagline {
    position: absolute;
    left: 476px; top: 87px;
    font-family: "Damion", cursive;
    font-size: 26px;
    color: var(--tagline);
    text-shadow: 1px 1px 0 rgba(0,0,0,.55);
    white-space: nowrap;
  }
  .search {
    position: absolute;
    left: 901px; top: 52px;
    display: flex; align-items: center;
  }
  .search-field {
    width: 173px; height: 29px;
    border-radius: 15px;
    background: var(--cream);
    padding-left: 17px;
    font-size: 17px;
    line-height: 29px;
    color: var(--ink);
  }
  .search-go {
    margin-left: 10px;
    font-size: 18px;
    color: var(--cream);
  }
</style>
</head>
<body>
  <header class="header-variant header-variant--brown">
    <div class="header-panel">
      <div class="brand"><span class="brand-mark"></span>Dusty Spur Outfitters</div>
      <p class="tagline">Brand-New Retro Styled Western Wear</p>
      <div class="search"><div class="search-field">Search...</div><span class="search-go">GO!</span></div>
    </div>
  </header>

  <header class="header-variant header-variant--charcoal">
    <div class="header-panel">
      <div class="brand"><span class="brand-mark"></span>Dusty Spur Outfitters</div>
      <p class="tagline">Brand-New Retro Styled Western Wear</p>
      <div class="search"><div class="search-field">Search...</div><span class="search-go">GO!</span></div>
    </div>
  </header>

  <header class="header-variant header-variant--blue">
    <div class="header-panel">
      <div class="brand"><span class="brand-mark"></span>Dusty Spur Outfitters</div>
      <p class="tagline">Brand-New Retro Styled Western Wear</p>
      <div class="search"><div class="search-field">Search...</div><span class="search-go">GO!</span></div>
    </div>
  </header>
</body>
</html>
```